Packaging label design for Crystal water bottles

Hello, I am new to plotquarry and I am needing to have my packaging label designed for the crystal water bottles I'm manufacturing. The product name is Velumo Morrow Tide, the company is PELLVOT. The packaging is tube shaped cardboard like container, similar to what scotch bottles come in. I have included the diecut and the sample box that the manufacturer sent to me. Also included a photo of a concept idea and any logos or photos you may need.The font that is used for my logo is Pristina, if that can be used for everything but PELLVOT. (I used Proxima Nova for that)I would like the information on it to be: (and again this is just a concept I am open to adjustments and change) Morrow Tide- on the lid sectionAkasha by PELLVOT (I'm thinking that I might want this one a bit smaller and off set like a signature)500mlHighland, UT 84003www.akashacrystalenergy.comAnd have sacred geometry art on it such as Metatrons Cube, Fibonacci Spiral, or any other sacred geometry that might be appropriate or fitting.Again I am open to other options if you feel like you have a great idea for something different. Also i'm not sure if all the photos uploaded correctly, so let me know if one of them didn't work. Thank you.

```html
<!DOCTYPE html>
<html lang="en">
<head>
<meta charset="utf-8">
<title>Velumo Morrow Tide – Tube Label</title>
<link href="https://fonts.googleapis.com/css2?family=Cinzel:wght@700&family=Open+Sans:wght@400&display=swap" rel="stylesheet">
<style>
  :root{
    --paper:#ffffff;
    --frame:#555555;
    --gold-light:#fdd888;
    --gold-band:#cfab6a;
    --geo-tone:#e3bf7c;
    --ink:#3a3a3a;
    --name-ink:#111111;
    --spec-blue:#29abe2;
  }
  html,body{margin:0;padding:0;overflow:hidden;background:var(--paper);}
  .sheet{display:block;width:894px;height:1200px;}
  .spec-text{font-family:"Open Sans",sans-serif;font-size:16px;fill:var(--spec-blue);}
  .spec-line{stroke:var(--spec-blue);stroke-width:0.8;fill:none;}
  .lid-title{font-family:"Cinzel",serif;font-weight:700;font-size:60px;fill:var(--ink);letter-spacing:2px;}
  .brand-name{font-family:"Open Sans",sans-serif;font-weight:400;fill:var(--name-ink);}
  .info-text{font-family:"Open Sans",sans-serif;font-size:16px;fill:var(--ink);letter-spacing:0.8px;}
  .cap-light{fill:var(--gold-light);stroke:#666;stroke-width:0.6;}
  .cap-dark{fill:var(--gold-band);stroke:#666;stroke-width:0.6;}
  .band{fill:var(--gold-band);stroke:#444;stroke-width:0.6;}
  .body-panel{fill:var(--gold-light);stroke:#444;stroke-width:0.6;}
</style>
</head>
<body>
<svg class="sheet" viewBox="0 0 850 1141" xmlns="http://www.w3.org/2000/svg">
  <defs>
    <radialGradient id="geo-glow">
      <stop offset="0" stop-color="var(--geo-tone)" stop-opacity="0.55"/>
      <stop offset="0.45" stop-color="var(--geo-tone)" stop-opacity="0.25"/>
      <stop offset="0.8" stop-color="var(--geo-tone)" stop-opacity="0.6"/>
      <stop offset="0.9" stop-color="var(--geo-tone)" stop-opacity="0.3"/>
      <stop offset="1" stop-color="var(--geo-tone)" stop-opacity="0"/>
    </radialGradient>
    <clipPath id="lid-clip"><rect x="118" y="376" width="650" height="139"/></clipPath>
    <clipPath id="body-clip"><rect x="118" y="515" width="650" height="499"/></clipPath>
  </defs>

  <rect x="0.5" y="0.5" width="849" height="1140" fill="var(--paper)" stroke="var(--frame)" stroke-width="1"/>

  <text class="spec-text" x="400" y="33" text-anchor="middle">D:Φ83mm</text>

  <!-- lid caps -->
  <g class="cap cap-mark">
    <circle class="cap-light" cx="237" cy="176" r="95"/>
    <text class="brand-name" x="237" y="190" font-size="40" text-anchor="middle">Velumo</text>
  </g>
  <g class="cap cap-name">
    <circle class="cap-dark" cx="560" cy="176" r="95"/>
    <text class="brand-name" x="560" y="180" font-size="40" text-anchor="middle">Velumo</text>
    <text class="brand-name" x="560" y="214" font-size="19" text-anchor="middle">Morrow Tide</text>
  </g>

  <!-- tube wrap -->
  <g class="wrap">
    <rect class="band" x="118" y="348" width="650" height="28"/>
    <rect class="body-panel" x="118" y="376" width="650" height="139"/>
    <g clip-path="url(#lid-clip)">
      <circle cx="443" cy="445" r="150" fill="url(#geo-glow)" role="img" aria-label="Faint sacred geometry pattern (Metatron's cube) behind the lid title"/>
    </g>
    <text class="lid-title" x="443" y="478" text-anchor="middle">MORROW TIDE</text>

    <rect class="body-panel" x="118" y="515" width="650" height="499"/>
    <g clip-path="url(#body-clip)">
      <circle cx="150" cy="760" r="205" fill="url(#geo-glow)" role="img" aria-label="Sacred geometry circle pattern, left side"/>
      <circle cx="735" cy="760" r="205" fill="url(#geo-glow)" role="img" aria-label="Sacred geometry circle pattern, right side"/>
    </g>

    <g class="signature" transform="translate(452 725) rotate(-90)">
      <text class="brand-name" x="0" y="0" font-size="62" text-anchor="middle">Velumo</text>
      <text class="brand-name" x="128" y="36" font-size="20" text-anchor="end">By PELLVOT</text>
    </g>

    <text class="info-text" x="443" y="953" text-anchor="middle">500ml</text>
    <text class="info-text" x="443" y="977" text-anchor="middle">Fernvale UT 84990</text>
    <text class="info-text" x="443" y="1001" text-anchor="middle">www.velumomorrowtide.com</text>

    <rect class="band" x="118" y="1014" width="650" height="28"/>
  </g>

  <!-- dimension marks -->
  <g class="dimensions">
    <text class="spec-text" x="44" y="367">12mm</text>
    <text class="spec-text" x="44" y="1033">12mm</text>

    <line class="spec-line" x1="776" y1="376" x2="776" y2="1014"/>
    <line class="spec-line" x1="768" y1="376" x2="806" y2="376"/>
    <line class="spec-line" x1="768" y1="515" x2="806" y2="515"/>
    <line class="spec-line" x1="768" y1="1014" x2="806" y2="1014"/>
    <text class="spec-text" transform="translate(794 432) rotate(90)">H:60mm</text>
    <text class="spec-text" transform="translate(794 845) rotate(90)">H:215mm</text>

    <line class="spec-line" x1="118" y1="1078" x2="768" y2="1078"/>
    <line class="spec-line" x1="118" y1="1042" x2="118" y2="1080"/>
    <line class="spec-line" x1="768" y1="1042" x2="768" y2="1080"/>
    <text class="spec-text" x="450" y="1072" text-anchor="middle" font-size="17">W:280mm</text>
  </g>
</svg>
</body>
</html>
```